New Year's card HTML

can you produce a best new years wishes 2018 design in HTML for our website as what I would like to send by email towards my network of candidates / customers ...

It must be wow, inspiring , design, meaningfull... MMM those people care about me, or those people will help me to go the extra mile, to help me to achieve my career goals, Your best move, enhance my possibilities, bring the love back

Target Market(s)

CEo's / CMO's/ HRDirectors network of 450k

Coding

Coded - Design and coding required

Number of Pages Required

1 page

Colors

Designer to choose colors to be used in the design.

Requirements
Must have
• Logo / visual / website adress www.moravintel.com and a call to action
Should not have
• no sound as our business is confidential

```html
<!DOCTYPE html>
<html lang="en">
<head>
<meta charset="utf-8">
<title>Happy New Year 2018 – Moravintel</title>
<link rel="stylesheet" href="https://fonts.googleapis.com/css2?family=Lobster&family=Signika:wght@500&family=Oswald:wght@600&family=Cinzel:wght@500&display=swap">
<style>
  :root {
    --sun-light: #fdd233;
    --sun-mid: #f8b21c;
    --sun-deep: #f08a12;
    --card-white: #ffffff;
    --ring-red: #ee2a24;
    --ring-green: #2eaa2a;
    --ink-green: #0f4414;
    --accent-pink: #f2365f;
    --button-red: #e3212d;
    --button-rim: #d9d9d9;
    --brand-white: #ffffff;
  }
  * { margin: 0; padding: 0; box-sizing: border-box; }
  html, body { width: 1200px; height: 1200px; overflow: hidden; }
  .greeting-card {
    position: relative;
    width: 1200px;
    height: 1200px;
    overflow: hidden;
    background: radial-gradient(circle at 50% 55%, var(--sun-light) 0%, var(--sun-mid) 45%, var(--sun-deep) 100%);
  }
  .bunting, .lantern, .crest-mark { position: absolute; }
  .bunting { left: 0; top: 20px; width: 1200px; height: 320px; }
  .lantern-left {
    left: 48px; top: 630px; width: 130px; height: 330px;
    border-radius: 40px 40px 20px 20px;
    background: linear-gradient(180deg, #e8262c 0%, #f7c21b 40%, #2f9e35 75%, #f3a020 100%);
    opacity: .95;
  }
  .lantern-right {
    left: 950px; top: 300px; width: 170px; height: 400px;
    border-radius: 50px 50px 24px 24px;
    background: linear-gradient(180deg, #e8262c 0%, #f7c21b 40%, #2f9e35 75%, #f3a020 100%);
    opacity: .95;
  }
  .crest-mark {
    left: 570px; top: 70px; width: 84px; height: 84px;
    border-radius: 50%;
    background: var(--ink-green);
  }
  .wish-disc {
    position: absolute;
    left: 225px; top: 267px;
    width: 770px; height: 770px;
    border-radius: 50%;
    background: var(--card-white);
    box-shadow: 0 0 0 14px transparent;
  }
  .wish-ring { position: absolute; left: 205px; top: 247px; width: 810px; height: 810px; }
  .wish-text {
    position: absolute;
    left: 225px; width: 770px;
    text-align: center;
    color: var(--ink-green);
    font-family: "Lobster", cursive;
  }
  .wish-happy { top: 370px; font-size: 84px; line-height: 1; }
  .wish-title { top: 490px; font-size: 140px; line-height: 1; }
  .wish-year {
    top: 668px; font-size: 178px; line-height: 1;
    font-family: "Signika", sans-serif; font-weight: 500;
    color: var(--accent-pink);
  }
  .cta-button {
    position: absolute;
    left: 428px; top: 925px;
    width: 350px; height: 124px;
    border-radius: 62px;
    background: linear-gradient(180deg, #f2f2f2, var(--button-rim));
    display: flex; align-items: center; justify-content: center;
    text-decoration: none;
    box-shadow: 0 6px 14px rgba(120, 60, 0, .25);
  }
  .cta-label {
    display: flex; align-items: center; justify-content: center;
    width: 318px; height: 92px;
    border-radius: 46px;
    background: linear-gradient(180deg, #f0353d, var(--button-red));
    color: var(--brand-white);
    font-family: "Oswald", sans-serif; font-weight: 600;
    font-size: 36px; letter-spacing: 1px;
  }
  .brand-line {
    position: absolute;
    left: 0; width: 1200px; top: 1090px;
    display: flex; align-items: center; justify-content: center; gap: 22px;
    color: var(--brand-white);
  }
  .brand-dot { width: 44px; height: 44px; border-radius: 50%; background: var(--brand-white); }
  .brand-name {
    font-family: "Cinzel", serif; font-weight: 500;
    font-size: 60px; letter-spacing: 2px; line-height: 1;
  }
</style>
</head>
<body>
<main class="greeting-card">
  <svg class="bunting" viewBox="0 0 1200 320" role="img" aria-label="Colourful festive bunting flags strung across the top">
    <defs>
      <linearGradient id="buntingTone" x1="0" x2="1" y1="0" y2="0">
        <stop offset="0" stop-color="#2a9fe0"/>
        <stop offset=".35" stop-color="#e8312b"/>
        <stop offset=".65" stop-color="#3aae3a"/>
        <stop offset="1" stop-color="#e8312b"/>
      </linearGradient>
    </defs>
    <path d="M0 140 Q600 270 1200 40 L1200 170 Q600 360 0 280 Z" fill="url(#buntingTone)" opacity=".85"/>
  </svg>

  <div class="crest-mark" aria-hidden="true"></div>

  <svg class="wish-ring" viewBox="0 0 810 810" aria-hidden="true">
    <path d="M405 15 A390 390 0 0 0 90 640" fill="none" stroke="var(--ring-red)" stroke-width="18" stroke-linecap="round"/>
    <path d="M795 405 A390 390 0 0 1 480 790" fill="none" stroke="var(--ring-green)" stroke-width="16" stroke-linecap="round"/>
    <path d="M405 15 A390 390 0 0 1 760 260" fill="none" stroke="var(--ring-red)" stroke-width="14" stroke-linecap="round"/>
  </svg>
  <div class="wish-disc"></div>

  <div class="lantern lantern-left" role="img" aria-label="Striped paper lantern with hanging ribbons"></div>
  <div class="lantern lantern-right" role="img" aria-label="Striped paper lantern with hanging ribbons"></div>

  <h2 class="wish-text wish-happy">Happy</h2>
  <h1 class="wish-text wish-title">New Year</h1>
  <p class="wish-text wish-year">2018</p>

  <a class="cta-button" href="https://www.moravintel.com"><span class="cta-label">VISIT OUR SITE</span></a>

  <div class="brand-line">
    <span class="brand-dot" aria-hidden="true"></span>
    <span class="brand-name">MORAVINTEL</span>
  </div>
</main>
</body>
</html>
```